Need a Wordpress website for my HVAC company

I need a Wordpress website created for an HVAC company in a competitive market.
Following are some websites I like:
My current website is www.borvicoheating.com - we also have a facebook page with some pictures

We are an airconditioning and heating company that does both residential and commmercial work.
We need the following info on our website:
-mobile friendly
-Schedule an appt -repair/maintnenace/installation (i would like this option to always be on the page even if they scroll down.)
-24 hour service
-coupons /promotions
-financing
-reviews/testimonials
-about
-blog
-Our service area
The following are services we provide:
-Air conditioning - Installation/Service/Maintenance/new construction
-Heating - Installation/Service/Maintenance/new construction ( gas furnace, 2 stage furnace, electric heat)
-Duct - Repair/Replacement/Istallation - (zone systems)
-thermostats (wifi)
-Heat pump
-Air handler
-self communicating systems
-carbon monoxide testing
-hail damage
-duct sealing
-insulation
-Air cleaners - UV Air purifiers
-humidifiers

I would also like Quilbo SEO add on

Target Market(s)

Anyone who needs our services HVAC contractor

Industry/Entity Type

Hvac

Contact Information for Business Card

Phone:480-555-2046
website:www.borvicoheating.com
email pmarsh@borvicoheating.com

Coding

Coded - Design and coding required

Number of Pages Required

5+ page

Font styles to use
Serif
Sans Serif

Requirements
Must have
• I wrote in brief. I already have Webly Nest. Long story I paid for 3 years already. I need someone to put website there. Ive never used Wordpress but would like a template page so I can easily add services.
Nice to have
• Clean, bright, original

```html
<!DOCTYPE html>
<html lang="en">
<head>
<meta charset="utf-8">
<title>Borvico Heating – Air Conditioning &amp; Heating</title>
<link href="https://fonts.googleapis.com/css2?family=Open+Sans:wght@400;600;700&family=Roboto:wght@400;500;700&display=swap" rel="stylesheet">
<style>
:root{
  --red:#c8202f;
  --blue:#11579c;
  --blue-dark:#0f4d8a;
  --green:#1f8a49;
  --green-text:#1a8a3e;
  --ink:#333;
  --muted:#777;
  --grey-bg:#f3f4f6;
  --line:#ddd;
  --white:#fff;
}
*{box-sizing:border-box;margin:0;padding:0}
html,body{width:1200px;height:2857px;overflow:hidden}
body{position:relative;font-family:"Open Sans",Arial,sans-serif;color:var(--ink);background:var(--white)}
.abs{position:absolute}
.ph{position:absolute}

/* top bar */
.topbar{left:0;top:0;width:1200px;height:38px;background:var(--red)}
.topbar .socials{left:781px;top:8px;display:flex;gap:4px}
.topbar .socials span{width:22px;height:22px;border:1.5px solid var(--white);border-radius:50%;display:block}
.topbar .call{left:930px;top:10px;color:var(--white);font:600 14px "Roboto",sans-serif;display:flex;align-items:center;gap:8px}

/* nav */
.nav{left:0;top:38px;width:1200px;height:82px;background:var(--white)}
.brand{left:92px;top:22px;display:flex;align-items:center;gap:8px;color:var(--red);font:700 24px "Open Sans",sans-serif}
.brand i{width:28px;height:28px;border-radius:50%;background:var(--red);display:block}
.menu{left:318px;top:40px;display:flex;font:600 12px "Roboto",sans-serif;color:#444;letter-spacing:.2px}
.menu a{color:inherit;text-decoration:none;text-transform:uppercase;margin-right:36px}
.menu a.active{color:var(--red)}
.search{left:1076px;top:22px;width:38px;height:38px;border:2px solid var(--green);border-radius:50%}

/* hero */
.hero{left:0;top:120px;width:1200px;height:493px;background:linear-gradient(100deg,#bfc2c4 0%,#9fa4a6 30%,#5f7d45 55%,#4f7d2e 100%)}
.hero-title{right:120px;top:276px;color:var(--white);font:700 30px "Roboto",sans-serif;letter-spacing:.5px}
.hero-sub{right:120px;top:330px;width:380px;text-align:right;color:var(--white);font:400 15px/26px "Open Sans",sans-serif}
.hero-btn{left:901px;top:400px;width:179px;height:38px;border:1.5px solid var(--white);color:var(--white);font:500 13px "Roboto",sans-serif;display:flex;align-items:center;justify-content:center;text-transform:uppercase}
.arrow{top:340px;width:52px;height:52px;border:2px solid var(--white);border-radius:50%;display:flex;align-items:center;justify-content:center}

/* service cards */
.card{top:552px;width:331px;height:261px;border:4px solid rgba(255,255,255,.35);color:var(--white);text-align:center;padding-top:80px}
.card.red{left:88px;background:var(--red);outline:2px solid #b51a28}
.card.blue{left:436px;background:var(--blue);outline:2px solid #0d467f}
.card.green{left:785px;background:var(--green);outline:2px solid #187a3d}
.card h3{font:600 17px "Roboto",sans-serif;text-transform:uppercase;margin-bottom:14px}
.card p{font:400 12px/24px "Open Sans",sans-serif;padding:0 30px}
.card .btn{margin:16px auto 0;width:108px;height:32px;border:1.5px solid var(--white);font:400 12px "Roboto",sans-serif;display:flex;align-items:center;justify-content:center;text-transform:uppercase}
.badge{top:498px;width:116px;height:116px;border-radius:50%;border:3px solid var(--white);display:flex;align-items:center;justify-content:center}

/* welcome */
.welcome-title{left:88px;top:878px;font:400 24px "Open Sans",sans-serif;color:#444}
.welcome-tag{left:88px;top:920px;font:700 15px "Open Sans",sans-serif;color:var(--green-text);text-transform:uppercase}
.welcome-text{left:88px;top:960px;width:600px;font:400 12px/24px "Open Sans",sans-serif;color:#666}
.outline-btn{left:88px;top:1105px;width:152px;height:42px;border:1.5px solid var(--green);color:var(--green-text);font:400 13px "Roboto",sans-serif;display:flex;align-items:center;justify-content:center;text-transform:uppercase}

/* services */
.services{left:0;top:1200px;width:1200px;height:644px;background:var(--grey-bg)}
.sec-title{width:1200px;left:0;text-align:center;font:400 25px "Open Sans",sans-serif;color:#444}
.sec-sub{width:1200px;left:0;text-align:center;font:400 12px "Open Sans",sans-serif;color:#666}
.svc{width:240px;font:400 12px/24px "Open Sans",sans-serif;color:#777}
.svc h4{font:600 14px "Roboto",sans-serif;color:#444;text-transform:uppercase;margin-bottom:6px;line-height:18px}
.svc.l{text-align:right;left:93px}
.svc.r{text-align:left;left:872px}
.ico{width:72px;height:72px;border-radius:50%;background:var(--white);border:1.5px solid;display:flex;align-items:center;justify-content:center}
.ico.red{border-color:var(--red)}.ico.blue{border-color:var(--blue)}.ico.green{border-color:var(--green)}
.view-all{left:491px;top:1749px;width:216px;height:45px;border:1.5px solid var(--red);color:var(--red);background:var(--white);font:400 13px "Roboto",sans-serif;display:flex;align-items:center;justify-content:center;gap:10px;text-transform:uppercase}

/* coupon band */
.coupon{left:0;top:1848px;width:1200px;height:202px;background:var(--blue-dark)}
.coupon .dash{left:0;width:1200px;border-top:2px dashed rgba(255,255,255,.6)}
.coupon-title{left:432px;top:1887px;color:var(--white);font:500 24px "Roboto",sans-serif;text-transform:uppercase}
.coupon-sub{left:432px;top:1925px;color:var(--white);font:600 20px "Open Sans",sans-serif}
.coupon-price{left:432px;top:1968px;color:var(--white);font:700 42px "Roboto",sans-serif}
.coupon-price small{font:400 17px "Open Sans",sans-serif}
.coupon-btn{left:907px;top:1926px;width:198px;height:51px;border:1.5px solid var(--white);color:var(--white);font:600 15px "Roboto",sans-serif;display:flex;align-items:center;justify-content:center;text-transform:uppercase}

/* testimonials */
.quote{width:222px}
.quote p{font:400 12px/24px "Open Sans",sans-serif;color:#666}
.quote p b{font:700 22px/10px Georgia,serif;color:#555;margin-right:6px}
.quote .who{margin-top:18px;font:600 12px "Roboto",sans-serif;color:var(--blue);text-transform:uppercase}
.quote .date{margin-top:6px;font:400 11px "Roboto",sans-serif;color:#444;text-transform:uppercase}
.quote .stars{margin-top:3px;color:#e6b31e;font-size:11px;letter-spacing:2px}
.avatar{width:84px;height:84px;border-radius:50%;background:linear-gradient(#c9b8a6,#8c7460)}

/* partner strip */
.partners{left:0;top:2438px;width:1200px;height:105px;background:var(--grey-bg)}
.partner{top:2475px;font:700 25px "Roboto",sans-serif;color:#666}
.chev{top:2478px;color:#999;font:400 26px "Roboto",sans-serif}

/* footer */
.footer{left:0;top:2543px;width:1200px;height:247px;background:var(--grey-bg)}
.f-head{top:2575px;font:600 15px "Roboto",sans-serif;color:#444;text-transform:uppercase}
.f-item{left:394px;font:400 11px/16px "Open Sans",sans-serif;color:#777;display:flex;gap:12px}
.f-item svg{flex:none;margin-top:2px}
.f-text{font:400 11px/18px "Open Sans",sans-serif;color:#888}
.f-input{left:627px;top:2672px;width:211px;height:32px;background:var(--white);border:1px solid var(--line);font:400 11px "Open Sans",sans-serif;color:#555;padding:9px 10px}
.f-sub{left:629px;top:2714px;width:78px;height:25px;background:var(--blue);color:var(--white);font:600 9px "Roboto",sans-serif;display:flex;align-items:center;justify-content:center;text-transform:uppercase}
.f-soc{top:2695px;width:34px;height:34px;border:1.5px solid #999;border-radius:50%}
.copyright{left:0;top:2790px;width:1200px;height:67px;background:var(--red);color:var(--white);font:400 12px "Open Sans",sans-serif;display:flex;align-items:center;justify-content:center}
</style>
</head>
<body>

<!-- top bar -->
<div class="abs topbar">
  <div class="abs socials"><span></span><span></span><span></span><span></span><span></span></div>
  <div class="abs call">
    <svg width="14" height="14" viewBox="0 0 24 24"><path fill="#fff" d="M6.6 10.8a15.1 15.1 0 0 0 6.6 6.6l2.2-2.2c.3-.3.7-.4 1-.2 1.1.4 2.3.6 3.6.6.6 0 1 .4 1 1V20c0 .6-.4 1-1 1A17 17 0 0 1 3 4c0-.6.4-1 1-1h3.5c.6 0 1 .4 1 1 0 1.3.2 2.5.6 3.6.1.3 0 .7-.2 1z"/></svg>
    CALL US : (480)-555-2046
  </div>
</div>

<!-- navigation -->
<header class="abs nav">
  <div class="abs brand"><i></i>Borvico Heating</div>
  <nav class="abs menu">
    <a class="active" href="#">Home</a><a href="#">About Us</a><a href="#">24 Hour Services</a><a href="#">Coupons</a><a href="#">Financing</a><a href="#">Reviews</a><a href="#">Blog</a><a href="#">Contact Us</a>
  </nav>
  <div class="abs search">
    <svg width="34" height="34" viewBox="0 0 34 34"><circle cx="16" cy="16" r="5" fill="none" stroke="#1f8a49" stroke-width="2"/><line x1="19.5" y1="19.5" x2="23" y2="23" stroke="#1f8a49" stroke-width="2"/></svg>
  </div>
</header>

<!-- hero -->
<section class="ph hero" role="img" aria-label="Photo of outdoor air conditioning condenser units beside a house with green lawn"></section>
<h1 class="abs hero-title">BORVICO HEATING</h1>
<p class="abs hero-sub">Air conditioning and heating company that does both residential and commercial work</p>
<div class="abs hero-btn">Get an Appointment</div>
<div class="abs arrow" style="left:27px"><svg width="16" height="16" viewBox="0 0 16 16"><path d="M10 3 5 8l5 5" fill="none" stroke="#fff" stroke-width="2"/></svg></div>
<div class="abs arrow" style="left:1124px"><svg width="16" height="16" viewBox="0 0 16 16"><path d="M6 3l5 5-5 5" fill="none" stroke="#fff" stroke-width="2"/></svg></div>

<!-- service cards -->
<div class="abs card red"><h3>Repair</h3><p>Borvico Heating Services is the premier are residential heating, air conditioning, and energy Phoenix the comfort of your home.</p><div class="btn">Read More</div></div>
<div class="abs card blue"><h3>Maintenance</h3><p>Borvico Heating Services is the premier are residential heating, air conditioning, and energy Phoenix the comfort of your home.</p><div class="btn">Read More</div></div>
<div class="abs card green"><h3>Installation</h3><p>Borvico Heating Services is the premier are residential heating, air conditioning, and energy Phoenix the comfort of your home.</p><div class="btn">Read More</div></div>

<div class="abs badge" style="left:196px;background:var(--red)">
  <svg width="54" height="54" viewBox="0 0 54 54" fill="none" stroke="#fff" stroke-width="3" stroke-linecap="round"><path d="M12 42 34 20"/><circle cx="38" cy="16" r="7"/><path d="M14 12l28 28"/><path d="M10 16l6-6"/></svg>
</div>
<div class="abs badge" style="left:543px;background:var(--blue)">
  <svg width="54" height="54" viewBox="0 0 54 54" fill="none" stroke="#fff" stroke-width="3"><circle cx="27" cy="27" r="8"/><path d="M27 9v6M27 39v6M9 27h6M39 27h6M14 14l4 4M36 36l4 4M40 14l-4 4M18 36l-4 4"/></svg>
</div>
<div class="abs badge" style="left:892px;background:var(--green)">
  <svg width="54" height="54" viewBox="0 0 54 54" fill="none" stroke="#fff" stroke-width="3"><rect x="9" y="12" width="36" height="24" rx="2"/><path d="M21 44h12M27 36v8"/><circle cx="27" cy="24" r="5"/></svg>
</div>

<!-- welcome -->
<h2 class="abs welcome-title">Welcome Borvico Heating</h2>
<p class="abs welcome-tag">Your satisfaction is guaranteed....Our reputation depends on it</p>
<p class="abs welcome-text">Borvico Heating Services is the premier residential heating, air conditioning, and energy solutions provider in the greater Phoenix area. We can help you lower your energy bills, reduce your environmental impact, and increase the comfort of your home. We design, install, service, repair and maintain residential air conditioning, heating and ventilation systems that will provide comfort for you and your family. Our team of experienced related to airflow, air quality and temperature. Click here to learn more.</p>
<div class="abs outline-btn">Read More Info</div>
<div class="ph" style="left:800px;top:886px;width:238px;height:228px;border-radius:50%;background:radial-gradient(circle,#fff 45%,#f4e7c4 62%,#f0d9d9 75%,#fff 76%)" role="img" aria-label="24/7, 365 days service clock graphic"></div>

<!-- our services -->
<section class="abs services"></section>
<h2 class="abs sec-title" style="top:1230px">Our Services</h2>
<p class="abs sec-sub" style="top:1270px">Borvico Heating Services is the premier residential heating, air conditioning, and energy solutions</p>

<div class="abs svc l" style="top:1355px"><h4>Air Conditioning</h4>conditioning service when you need it, not when we feel like being open. Call now. No deserve need to wait!</div>
<div class="abs svc l" style="top:1503px"><h4>Heating</h4>conditioning service when you need it, not when we feel like being open. Call now. No deserve need to wait!</div>
<div class="abs svc l" style="top:1652px"><h4>Thermostats</h4>conditioning service when you need it, not when we feel like being open. Call now. No deserve need to wait!</div>
<div class="abs svc r" style="top:1355px"><h4>Heat Pump</h4>conditioning service when you need it, not when we feel like being open. Call now. No deserve need to wait!</div>
<div class="abs svc r" style="top:1503px"><h4>Insulation</h4>conditioning service when you need it, not when we feel like being open. Call now. No deserve need to wait!</div>
<div class="abs svc r" style="top:1652px"><h4>Hail Damage</h4>conditioning service when you need it, not when we feel like being open. Call now. No deserve need to wait!</div>

<div class="abs ico green" style="left:351px;top:1355px"><svg width="36" height="36" viewBox="0 0 36 36" fill="none" stroke="#1f8a49" stroke-width="2"><rect x="4" y="9" width="28" height="14" rx="2"/><path d="M8 18h20M10 27v3M18 27v3M26 27v3"/></svg></div>
<div class="abs ico blue" style="left:351px;top:1503px"><svg width="36" height="36" viewBox="0 0 36 36" fill="none" stroke="#11579c" stroke-width="2"><path d="M6 17 18 7l12 10v13H6z"/><path d="M18 28c-3 0-4-2-4-4 0-3 3-4 3-7 2 2 5 4 5 7 0 2-1 4-4 4z"/></svg></div>
<div class="abs ico red" style="left:351px;top:1652px"><svg width="36" height="36" viewBox="0 0 36 36" fill="none" stroke="#c8202f" stroke-width="2"><path d="M15 6a3 3 0 0 1 6 0v15a6 6 0 1 1-6 0z"/><circle cx="18" cy="26" r="2.5" fill="#c8202f"/><path d="M24 10h4M24 14h4M24 18h4"/></svg></div>
<div class="abs ico blue" style="left:770px;top:1355px"><svg width="36" height="36" viewBox="0 0 36 36" fill="#11579c"><circle cx="18" cy="18" r="3"/><path d="M18 4c4 0 4 8 0 11-4-3-4-11 0-11zM18 32c-4 0-4-8 0-11 4 3 4 11 0 11zM4 18c0-4 8-4 11 0-3 4-11 4-11 0zM32 18c0 4-8 4-11 0 3-4 11-4 11 0z"/></svg></div>
<div class="abs ico red" style="left:770px;top:1503px"><svg width="36" height="36" viewBox="0 0 36 36" fill="none" stroke="#c8202f" stroke-width="2"><ellipse cx="12" cy="18" rx="6" ry="10"/><path d="M12 8h16v20H12"/><ellipse cx="12" cy="18" rx="2" ry="4"/></svg></div>
<div class="abs ico green" style="left:770px;top:1652px"><svg width="36" height="36" viewBox="0 0 36 36" fill="none" stroke="#1f8a49" stroke-width="2"><path d="M10 20a6 6 0 0 1 1-12 8 8 0 0 1 15 2 5 5 0 0 1 0 10z"/><circle cx="12" cy="26" r="1.5"/><circle cx="18" cy="29" r="1.5"/><circle cx="24" cy="26" r="1.5"/></svg></div>

<div class="ph" style="left:453px;top:1390px;width:309px;height:325px;border-radius:14px;background:linear-gradient(180deg,#e8ecf2 0%,#c8d3e2 45%,#2b2f36 100%)" role="img" aria-label="Company service van, front view"></div>
<div class="abs view-all">View All Services <svg width="14" height="14" viewBox="0 0 14 14"><circle cx="7" cy="7" r="6" fill="none" stroke="#c8202f" stroke-width="1.5"/><path d="M6 4.5 8.5 7 6 9.5" fill="none" stroke="#c8202f" stroke-width="1.5"/></svg></div>

<!-- coupon band -->
<section class="abs coupon">
  <div class="abs dash" style="top:6px"></div>
  <div class="abs dash" style="bottom:6px"></div>
</section>
<div class="ph" style="left:171px;top:1867px;width:210px;height:167px;border-radius:50%;background:radial-gradient(circle,#3a6fb0 0%,#1f5a9a 60%,#0f4d8a 100%)" role="img" aria-label="Cartoon technician mascot giving a thumbs up"></div>
<h2 class="abs coupon-title">Coupons &amp; Promotions</h2>
<p class="abs coupon-sub">Free A/C or Heating Services Call with Repair</p>
<p class="abs coupon-price">$20%<small>off of your next Repair</small></p>
<div class="abs coupon-btn">View Details</div>

<!-- testimonials -->
<h2 class="abs sec-title" style="top:2115px">Customer Testimonials</h2>
<p class="abs sec-sub" style="top:2156px">Borvico Heating Services is the premier residential heating, air conditioning, and energy solutions</p>

<div class="ph avatar" style="left:88px;top:2219px" role="img" aria-label="Customer portrait"></div>
<div class="abs quote" style="left:194px;top:2226px"><p><b>“</b>Our technicians do not work on commission, which allows us to keep our prices down. That also means you families or businesses comfort.</p><div class="who">Darren K. Queen Creek, AZ</div><div class="date">Posted on 25 Oct 2016</div><div class="stars">★★★★☆</div></div>

<div class="ph avatar" style="left:438px;top:2219px" role="img" aria-label="Customer portrait"></div>
<div class="abs quote" style="left:544px;top:2226px"><p><b>“</b>Our technicians do not work on commission, which allows us to keep our prices down. That also means you families or businesses comfort.</p><div class="who">Lena P. Gilbert, AZ</div><div class="date">Posted on 25 Oct 2016</div><div class="stars">★★★★☆</div></div>

<div class="ph avatar" style="left:788px;top:2219px" role="img" aria-label="Customer portrait"></div>
<div class="abs quote" style="left:894px;top:2226px"><p><b>“</b>Our technicians do not work on commission, which allows us to keep our prices down. That also means you families or businesses comfort.</p><div class="who">Omar T. Scottsdale, AZ</div><div class="date">Posted on 25 Oct 2016</div><div class="stars">★★★★☆</div></div>

<!-- partners -->
<section class="abs partners"></section>
<span class="abs chev" style="left:66px">‹</span>
<span class="abs partner" style="left:109px">Tunecast</span>
<span class="abs partner" style="left:278px">Quadrasoft</span>
<span class="abs partner" style="left:459px">Snapgram</span>
<span class="abs partner" style="left:622px">Pixelvault</span>
<span class="abs partner" style="left:810px">Tilebox</span>
<span class="abs partner" style="left:973px">Snapgram</span>
<span class="abs chev" style="left:1120px">›</span>

<!-- footer -->
<footer class="abs footer"></footer>
<div class="ph" style="left:118px;top:2562px;width:225px;height:219px;border-radius:50%;background:radial-gradient(circle,#3a6fb0 0%,#9fb6d3 65%,#f3f4f6 100%)" role="img" aria-label="Cartoon technician mascot giving a thumbs up"></div>

<h3 class="abs f-head" style="left:394px">Contact Us</h3>
<div class="abs f-item" style="top:2608px"><svg width="12" height="12" viewBox="0 0 24 24"><path fill="#777" d="M6.6 10.8a15.1 15.1 0 0 0 6.6 6.6l2.2-2.2c.3-.3.7-.4 1-.2 1.1.4 2.3.6 3.6.6.6 0 1 .4 1 1V20c0 .6-.4 1-1 1A17 17 0 0 1 3 4c0-.6.4-1 1-1h3.5c.6 0 1 .4 1 1 0 1.3.2 2.5.6 3.6.1.3 0 .7-.2 1z"/></svg>(480)-555-2046 (Phone)</div>
<div class="abs f-item" style="top:2638px"><svg width="12" height="12" viewBox="0 0 24 24"><rect x="3" y="8" width="18" height="10" rx="1" fill="#777"/><rect x="7" y="3" width="10" height="6" fill="#777"/></svg>(480)-555-2046 (Fax)</div>
<div class="abs f-item" style="top:2668px"><svg width="12" height="12" viewBox="0 0 24 24"><rect x="2" y="5" width="20" height="14" fill="none" stroke="#777" stroke-width="2"/><path d="m2 5 10 8 10-8" fill="none" stroke="#777" stroke-width="2"/></svg><span style="text-decoration:underline">info@borvicoheating.com</span></div>
<div class="abs f-item" style="top:2700px"><svg width="12" height="12" viewBox="0 0 24 24"><path fill="#777" d="M12 2a7 7 0 0 0-7 7c0 5 7 13 7 13s7-8 7-13a7 7 0 0 0-7-7zm0 9.5A2.5 2.5 0 1 1 12 6.5a2.5 2.5 0 0 1 0 5z"/></svg><span># 356 Lorem Ipsum Dummy<br>Lorem Ipsum</span></div>

<h3 class="abs f-head" style="left:627px">Newsletter</h3>
<p class="abs f-text" style="left:627px;top:2616px;width:220px">Register Your email address to get information ablout us</p>
<div class="abs f-input">Email Address</div>
<div class="abs f-sub">Subscribe</div>

<h3 class="abs f-head" style="left:888px">Follow Us</h3>
<p class="abs f-text" style="left:888px;top:2614px;width:200px">Lorem ipsum dolor sit amet, conse ctetur adipiscing elit. Nulla in purus nibh. Donec ornare</p>
<span class="abs f-soc" style="left:886px"></span>
<span class="abs f-soc" style="left:928px"></span>
<span class="abs f-soc" style="left:970px"></span>
<span class="abs f-soc" style="left:1012px"></span>
<span class="abs f-soc" style="left:1056px"></span>

<div class="abs copyright">© Copyright 2016 Borvico Heating .All Rights Reserved</div>

</body>
</html>
```